Los Brava Dip – CPG Website with WordPress - Store Locator: WP Maps plugin

Larkfield Food Company is a startup consumer packaged goods (CPG) brand launching its flagship product line — Los Brava Dip. We’re seeking a talented web designer to create a bold, professional, mobile-optimized website using WordPress with a WP Maps store locator to help customers find local retailers.

Our goal is to build a strong online presence that supports both retail growth and direct-to-consumer sales.

See Los Brava _Website_Design_Brief word document.

The website URL is https://losbravadip.example/

Target Market(s)

Consumers of gourmet salsa

Industry/Entity Type

Consumer Packaged Goods - Salsa manufacturer.

Coding

Coded - Design and coding required

Number of Pages Required

5+ page

Requirements
Must have
• The design of the Los Brava Dip website shall emulate the clean, polished aesthetic of Fennigo.example.

```html
<!DOCTYPE html>
<html lang="en">
<head>
<meta charset="utf-8">
<title>Los Brava Dip</title>
<link href="https://fonts.googleapis.com/css2?family=DM+Serif+Display&family=Outfit:wght@400;500;600&family=Roboto+Slab:wght@400;500;600&display=swap" rel="stylesheet">
<style>
:root{
  --red:#c8432b;
  --band-red:#c9432a;
  --green:#376b22;
  --yellow:#f7bb3c;
  --ink:#1d1d1d;
  --text:#333;
  --white:#fff;
  --rule:#e06060;
}
*{margin:0;padding:0;box-sizing:border-box}
html,body{width:1200px;height:3157px;overflow:hidden;background:var(--white)}
body{position:relative;font-family:"Outfit",sans-serif;color:var(--ink)}
.abs{position:absolute}
.serif{font-family:"DM Serif Display",serif;font-weight:400;text-transform:uppercase;letter-spacing:-.5px}

/* nav */
.nav{top:0;left:0;width:1200px;height:78px;background:var(--white)}
.nav a{position:absolute;top:30px;font-size:13.5px;letter-spacing:1.3px;color:var(--ink);text-decoration:none;font-weight:500}
.brand{position:absolute;font-family:"Outfit",sans-serif;font-weight:600;color:var(--red);white-space:nowrap}
.nav .brand{left:520px;top:20px;font-size:30px}
.nav .contact-btn{left:976px;top:21px;width:130px;height:34px;background:var(--red);color:var(--white);text-align:center;line-height:34px}

/* hero */
.hero{top:78px;left:0;width:1200px;height:613px;background:radial-gradient(circle at 55% 60%,#d9a43a 0,#b8632b 22%,#3b3534 45%,#2a2828 80%)}
.hero-rule{left:267px;width:620px;height:1px;background:rgba(255,255,255,.8)}
.hero-title{left:0;width:1200px;text-align:center;color:var(--white);font-size:58px;line-height:64px}
.shop-btn{left:516px;top:304px;width:157px;height:43px;border:2px solid var(--white);color:var(--white);font-size:14px;letter-spacing:1.3px;text-align:center;line-height:39px;font-weight:500}

/* section headings */
.section-rule{height:1.5px}
.section-title{text-align:center;font-size:38px;line-height:44px}

/* featured */
.product-photo{left:172px;top:876px;width:404px;height:374px;background:radial-gradient(ellipse at 50% 50%,#e8a33c 0,#d45a2f 35%,#8fae4b 60%,#fff 72%)}
.product-name{left:651px;top:938px;font-family:"Roboto Slab",serif;font-weight:500;font-size:34px;color:#2a2a2a;white-space:nowrap}
.product-copy{left:651px;top:995px;width:460px;font-size:19px;line-height:27.5px;color:var(--text);white-space:nowrap}
.outline-btn{border:2px solid var(--red);color:var(--red);text-align:center;font-size:13.5px;letter-spacing:1.3px;font-weight:600}

/* reviews */
.reviews{top:1329px;left:0;width:1200px;height:633px;background:var(--green)}
.panel{background:var(--white);border:2px solid #111;box-shadow:6px 6px 0 rgba(0,0,0,.35)}
.review-head{left:107px;top:1550px;width:996px;text-align:center;font-size:23px}
.review-head small{font-size:17px}
.stars{display:inline-flex;gap:3px;vertical-align:middle}
.stars i{width:15px;height:15px;background:#1b8f5a;display:block}
.review-card{top:1618px;width:291px;height:180px;background:var(--white);box-shadow:0 0 8px rgba(0,0,0,.15);padding:30px 34px}
.review-card h4{font-weight:400;font-size:16.5px;margin:14px 0 6px}
.review-card p{font-size:12.5px;line-height:19px;color:#444}
.review-card b{display:block;margin-top:10px;font-weight:600;font-size:14.5px}
.arrow{stroke:#888;stroke-width:2.5;fill:none}

/* recipes */
.recipes{top:1962px;left:0;width:1200px;height:695px;background:var(--yellow)}
.recipe-photo{left:145px;top:2163px;width:441px;height:378px;background:radial-gradient(ellipse at 45% 55%,#e9b04a 0,#d6875a 35%,#3c5a8c 62%,#253f78 100%)}
.recipe-title{left:662px;top:2205px;font-size:26.5px;font-weight:600;line-height:28.5px;letter-spacing:.5px}
.recipe-mark{left:662px;top:2270px;width:34px;height:2px;background:#d99a2b}
.recipe-copy{left:661px;top:2284px;width:420px;font-size:15.5px;line-height:27px;color:var(--text);white-space:nowrap}

/* follow band */
.follow{top:2657px;left:0;width:1200px;height:143px;background:var(--band-red)}
.follow-title{left:0;width:1215px;top:2711px;text-align:center;color:var(--white);font-size:29px;font-weight:600;letter-spacing:.5px}

/* footer */
.foot-head{font-size:20px;font-weight:600;letter-spacing:.5px;border-top:2px solid var(--red);padding-top:4px}
.foot-list{list-style:none;font-size:16px;line-height:28.8px;color:#333}
.social{width:38px;height:38px;border-radius:50%}
.copyright{left:0;width:1200px;top:3100px;text-align:center;font-size:13px;color:#333}
</style>
</head>
<body>

<header class="abs nav">
  <a style="left:101px">ABOUT</a>
  <a style="left:206px">PRODUCTS</a>
  <a style="left:341px">WHERE TO BUY</a>
  <span class="brand">Los Brava</span>
  <a style="left:750px">RECIPES</a>
  <a style="left:865px">REVIEW</a>
  <a class="contact-btn">CONTACT ›</a>
</header>

<section class="abs hero" role="img" aria-label="Overhead photo of tacos with bowls of chopped vegetables and salsa jars"></section>
<div class="abs hero-rule" style="top:156px"></div>
<div class="abs hero-rule" style="top:223px"></div>
<h1 class="abs hero-title serif" style="top:158px">Spice up your meals!<br>with Los Brava</h1>
<div class="abs shop-btn">SHOP NOW ›</div>

<div class="abs section-rule" style="top:765px;left:88px;width:995px;background:var(--rule)"></div>
<div class="abs section-rule" style="top:832px;left:88px;width:995px;background:var(--rule)"></div>
<h2 class="abs section-title serif" style="top:777px;left:88px;width:995px">Featured Product</h2>

<div class="abs product-photo" role="img" aria-label="Three salsa jars: all natural, habanero and verde"></div>
<h3 class="abs product-name">EL Los Brava multi Pack</h3>
<p class="abs product-copy">Lorem ipsum dolor sit amet, consectetur adipisc-<br>ing elit, sed do eiusmod tempor<br>Ancididunt ut labore et dolore magna aliqua. Quis<br>ipsum suspendisse ultrices gravida. Risus commo-<br>do viverra maecenas accumsan lacus vel facilisis.</p>
<div class="abs outline-btn" style="left:653px;top:1162px;width:182px;height:43px;line-height:39px">VIEW PRODUCTS</div>

<section class="abs reviews"></section>
<div class="abs section-rule" style="top:1391px;left:98px;width:994px;background:rgba(255,255,255,.85)"></div>
<div class="abs section-rule" style="top:1459px;left:98px;width:994px;background:rgba(255,255,255,.85)"></div>
<h2 class="abs section-title serif" style="top:1403px;left:98px;width:994px;color:var(--white)">Reviews</h2>
<div class="abs panel" style="left:107px;top:1501px;width:996px;height:387px"></div>
<div class="abs review-head">Let Customer Speak for us <span class="stars"><i></i><i></i><i></i><i></i><i></i></span> <small>from 448 reviews</small></div>

<article class="abs review-card" style="left:161px">
  <span class="stars"><i></i><i></i><i></i><i></i><i></i></span>
  <h4>Awesome taste, fresh</h4>
  <p>Lorem ipsum dolor sit amet, consectetur adipiscing elit, sed do eiusmod temp</p>
  <b>Mara Ellis</b>
</article>
<article class="abs review-card" style="left:472px">
  <span class="stars"><i></i><i></i><i></i><i></i><i></i></span>
  <h4>Awesome taste, fresh</h4>
  <p>Lorem ipsum dolor sit amet, consectetur adipiscing elit, sed do eiusmod temp</p>
  <b>Mara Ellis</b>
</article>
<article class="abs review-card" style="left:779px">
  <span class="stars"><i></i><i></i><i></i><i></i><i></i></span>
  <h4>Awesome taste, fresh</h4>
  <p>Lorem ipsum dolor sit amet, consectetur adipiscing elit, sed do eiusmod temp</p>
  <b>Mara Ellis</b>
</article>
<svg class="abs" style="left:578px;top:1815px" width="64" height="30" viewBox="0 0 64 30"><path class="arrow" d="M16 3 L6 15 L16 27"/><path class="arrow" d="M48 3 L58 15 L48 27"/></svg>

<section class="abs recipes"></section>
<div class="abs section-rule" style="top:2026px;left:113px;width:995px;background:#1d1d1d"></div>
<div class="abs section-rule" style="top:2094px;left:113px;width:995px;background:#1d1d1d"></div>
<h2 class="abs section-title serif" style="top:2038px;left:113px;width:995px">Recipes</h2>
<div class="abs panel" style="left:110px;top:2138px;width:998px;height:436px;box-shadow:6px 6px 0 rgba(90,70,0,.55)"></div>
<div class="abs recipe-photo" role="img" aria-label="Baked chicken topped with melted cheese and cilantro on a blue plate"></div>
<h3 class="abs recipe-title">BAKED CHICKEN WITH<br>SALSA AND SOUR CREAM</h3>
<div class="abs recipe-mark"></div>
<p class="abs recipe-copy">Looking for a weeknight dinner that's both effortless<br>and packed with flavor? This Baked Chicken with Salsa<br>and Sour Cream is a creamy, cheesy, oven-baked<br>comfort dish that's as satisfying as it is simple.<br>Seasoned with taco spices</p>
<div class="abs outline-btn" style="left:659px;top:2440px;width:159px;height:43px;line-height:39px">VIEW RECIPE</div>
<svg class="abs" style="left:986px;top:2476px" width="64" height="30" viewBox="0 0 64 30"><path class="arrow" d="M16 3 L6 15 L16 27"/><path class="arrow" d="M48 3 L58 15 L48 27"/></svg>

<section class="abs follow"></section>
<div class="abs section-rule" style="top:2699px;left:109px;width:995px;background:rgba(255,255,255,.85)"></div>
<div class="abs section-rule" style="top:2765px;left:109px;width:995px;background:rgba(255,255,255,.85)"></div>
<h2 class="abs follow-title">FOLLOW US ON SOCIAL</h2>

<footer>
  <span class="brand" style="left:129px;top:2895px;font-size:38px">Los Brava</span>
  <span class="abs social" style="left:175px;top:2979px;background:var(--red)"></span>
  <span class="abs social" style="left:228px;top:2982px;width:32px;height:32px;border:2px solid #222"></span>

  <h4 class="abs foot-head" style="left:396px;top:2857px">NAVIGATION</h4>
  <ul class="abs foot-list" style="left:396px;top:2898px">
    <li>About Us</li><li>Products</li><li>Recipes</li><li>Reviews</li>
  </ul>
  <ul class="abs foot-list" style="left:555px;top:2902px">
    <li>Privacy Policy</li><li>Shipping Policy</li><li>Terms and Conditions</li><li>Contact us</li>
  </ul>

  <h4 class="abs foot-head" style="left:795px;top:2857px">CONTACT US</h4>
  <svg class="abs" style="left:795px;top:2903px" width="32" height="32" viewBox="0 0 32 32"><circle cx="16" cy="16" r="16" fill="#333"/><rect x="8" y="10.5" width="16" height="11" fill="none" stroke="#fff" stroke-width="1.6"/><path d="M8 11 L16 17 L24 11" fill="none" stroke="#fff" stroke-width="1.6"/></svg>
  <span class="abs" style="left:833px;top:2906px;font-size:18px;color:#222">support@losbravadip.example</span>

  <div class="abs" style="left:0;top:3079px;width:1200px;height:1px;background:#ccc"></div>
  <p class="abs copyright">Copyright © 2025 Brightpane.&nbsp; All Right Reserved</p>
</footer>

</body>
</html>
```